Business Card - connecting 2 souls and beggining the journey of self discovery

Logo on the front
with tag line

On the back list of services and contact details

Seminars
workshops
Coaching
podcasts

Darren Whitlow
Health & Wellbeing Life Coach
0491 372 615
darren@brightcoreliving.example
brightcoreliving.example

Industry/Entity Type

Life Coaching

Contact Information for Business Card

I like the use of colour from the logo to be used. I'm not a fan of white.

Requirements
Must have
• My tagline: The journey home starts with you
Nice to have
• Use of colour that is in the mind body soul logo

```html
<!DOCTYPE html>
<html lang="en">
<head>
<meta charset="utf-8">
<title>Bright Core Living – Business Cards</title>
<link rel="stylesheet" href="https://fonts.googleapis.com/css2?family=Montserrat:wght@600&family=Roboto:wght@300;400&display=swap">
<style>
  :root {
    --backdrop: #262626;
    --tint-warm: #fbe7df;
    --tint-sun: #fbf1d8;
    --tint-fresh: #e2f2e6;
    --tint-cool: #ddf0ee;
    --ink: #4f4f4f;
    --brand-grey: #6f6f6f;
    --service-grey: #7d7d7d;
    --accent: #2a9d90;
    --mark: #8cc78a;
  }
  * { margin: 0; padding: 0; box-sizing: border-box; }
  html, body {
    width: 1200px;
    height: 1096px;
    overflow: hidden;
    background: var(--backdrop);
  }
  .canvas {
    position: relative;
    width: 1200px;
    height: 1096px;
  }
  .card {
    position: absolute;
    width: 550px;
    height: 317px;
    overflow: hidden;
  }
  .card--back {
    left: 491px;
    top: 207px;
    background: linear-gradient(120deg, var(--tint-warm) 0%, var(--tint-sun) 45%, var(--tint-fresh) 100%);
  }
  .card--front {
    left: 198px;
    top: 566px;
    background: linear-gradient(120deg, var(--tint-fresh) 0%, var(--tint-sun) 50%, var(--tint-cool) 100%);
  }

  .contact {
    position: absolute;
    left: 31px;
    top: 27px;
    font-family: "Roboto", sans-serif;
    font-weight: 400;
    font-size: 21.5px;
    line-height: 26.4px;
    color: var(--ink);
    list-style: none;
  }
  .brand-name {
    position: absolute;
    left: 0;
    width: 100%;
    text-align: center;
    font-family: "Montserrat", sans-serif;
    font-weight: 600;
    font-size: 38px;
    letter-spacing: -1.4px;
    color: var(--brand-grey);
    line-height: 1;
  }
  .card--back .brand-name { top: 192px; left: 12px; }
  .card--front .brand-name { top: 186px; }

  .services {
    position: absolute;
    top: 263px;
    left: 0;
    width: 100%;
    display: flex;
    justify-content: center;
    gap: 26px;
    padding-left: 22px;
    list-style: none;
    font-family: "Roboto", sans-serif;
    font-weight: 300;
    font-size: 21px;
    color: var(--service-grey);
  }
  .brand-mark {
    position: absolute;
    left: 212px;
    top: 40px;
  }
  .tagline {
    position: absolute;
    top: 236px;
    left: 0;
    width: 100%;
    text-align: center;
    font-family: "Roboto", sans-serif;
    font-weight: 400;
    font-size: 19px;
    color: var(--accent);
  }
  .web-address {
    position: absolute;
    top: 280px;
    left: 0;
    width: 100%;
    text-align: center;
    font-family: "Roboto", sans-serif;
    font-weight: 400;
    font-size: 18px;
    color: var(--ink);
  }
</style>
</head>
<body>
<main class="canvas">
  <section class="card card--back" aria-label="Card back">
    <ul class="contact">
      <li>Darren Whitlow</li>
      <li>Health &amp; Wellbeing Life Coach</li>
      <li>0491 372 615</li>
      <li>darren@brightcoreliving.example</li>
      <li>brightcoreliving.example</li>
    </ul>
    <p class="brand-name">Bright Core Living</p>
    <ul class="services">
      <li>Seminar</li>
      <li>Workshop</li>
      <li>Coaching</li>
      <li>Podcast</li>
    </ul>
  </section>

  <section class="card card--front" aria-label="Card front">
    <svg class="brand-mark" width="126" height="126" viewBox="0 0 126 126" aria-hidden="true">
      <circle cx="63" cy="63" r="63" fill="var(--mark)"/>
    </svg>
    <p class="brand-name">Bright Core Living</p>
    <p class="tagline">The journey home starts with you</p>
    <p class="web-address">www.brightcoreliving.example</p>
  </section>
</main>
</body>
</html>
```